Insurance Agency website design for Brellow Cover Insurance, LP

Build a website for Brellow Cover Insurance, LP which sells Homeowners, Auto, Renters, Condo, Flood, Disability, Life, Umbrella, and health insurance. We need the coolest insurance agency website out there to get quotes, contact us, or get additional information. Please list the following insurance companies we work with: Varnix, Ostle, Meridale Mutual, Quillor, Dunmarrow, KGZ, and Pellwick.

Make a design similar to https://www.fernagentry.com/

Selling personal insurance policies

```html
<!DOCTYPE html>
<html lang="en">
<head>
<meta charset="utf-8">
<title>Brellow Cover Insurance, LP</title>
<link href="https://fonts.googleapis.com/css2?family=Poppins:ital,wght@0,400;0,500;0,600;0,700;0,800;1,400&display=swap" rel="stylesheet">
<style>
:root{
  --blue:#1b6fd6;
  --blue-dark:#1559b0;
  --green:#3cb44a;
  --ink:#1f2430;
  --muted:#6b7280;
  --star:#f5a623;
  --light:#f2f4f7;
  --footer:#2a2c30;
  --footer-line:#3b3e44;
  --white:#ffffff;
}
*{box-sizing:border-box;margin:0;padding:0}
html,body{width:1200px;height:2704px;overflow:hidden}
body{font-family:"Poppins",sans-serif;color:var(--ink);background:var(--white);position:relative}
a{color:inherit;text-decoration:none}
.btn{display:inline-block;background:var(--green);color:var(--white);font-weight:600;border-radius:6px}

/* top bar */
.topbar{height:48px;background:var(--blue);color:var(--white);font-size:14px;display:flex;align-items:center;justify-content:space-between;padding:0 120px 0 100px}
.topbar .contacts{display:flex;gap:28px;align-items:center}
.topbar .contacts span{display:flex;align-items:center;gap:8px}
.topbar .agent a{color:#9ff0a6;font-weight:600}

/* nav */
.nav{height:96px;display:flex;align-items:center;justify-content:space-between;padding:0 120px 0 100px;background:var(--white)}
.brand{display:flex;align-items:center;gap:12px;color:var(--blue);font-weight:700;font-size:22px;line-height:1.1;width:260px}
.brand .mark{width:22px;height:22px;background:var(--green);border-radius:4px;flex:none}
.menu{display:flex;align-items:center;gap:34px;font-size:16px;font-weight:600}
.menu .active{border-bottom:2px solid var(--blue);color:var(--blue);padding-bottom:3px}
.menu .btn{padding:12px 22px;font-size:15px}

/* hero */
.hero{position:relative;height:508px}
.hero .photo{position:absolute;inset:0;background:linear-gradient(90deg,#f4f5f6 0%,#e9ebee 40%,#c9ced5 70%,#9aa3ae 100%)}
.hero .copy{position:absolute;left:100px;top:228px}
.hero h1{color:var(--blue);font-size:48px;font-weight:800;line-height:1.1}
.hero p{font-size:34px;font-weight:700;line-height:1.18;margin-top:12px;width:520px}
.hero .btn{margin-top:26px;padding:13px 24px;font-size:15px}

/* carriers */
.carriers{height:248px;padding-top:60px;text-align:center}
.carriers h2{font-size:28px;font-weight:600}
.carrier-row{display:flex;align-items:center;justify-content:center;gap:46px;margin-top:42px}
.carrier{font-size:24px;font-weight:700;color:var(--ink)}
.arrow{width:28px;height:28px}

/* welcome */
.welcome{height:452px;background:var(--blue);color:var(--white);text-align:center;padding-top:62px}
.welcome h2{font-size:42px;font-weight:700}
.welcome p{font-size:17px;line-height:1.65;width:880px;margin:26px auto 0}
.inquiry{width:690px;margin:36px auto 0;background:var(--green);border-radius:8px;padding:20px 0;font-size:22px;font-weight:700;line-height:1.4}

/* testimonials */
.reviews{height:548px;padding-top:56px;text-align:center;position:relative}
.reviews .kicker{color:var(--blue);font-size:24px;font-weight:600}
.reviews h2{font-size:42px;font-weight:700;margin-top:4px}
.cards{display:flex;justify-content:center;gap:60px;margin-top:40px}
.card{width:300px}
.stars{color:var(--star);font-size:24px;letter-spacing:4px}
.card h3{color:var(--blue);font-size:24px;font-weight:600;margin-top:4px}
.card .loc{font-size:17px;font-weight:500}
.card blockquote{font-size:14px;font-style:italic;color:var(--muted);line-height:1.55;margin-top:10px}
.side-arrow{position:absolute;top:252px}
.side-arrow.left{left:30px}
.side-arrow.right{right:34px}
.more{margin-top:54px;display:inline-block;border:2px solid var(--green);color:var(--green);font-weight:600;font-size:16px;padding:14px 42px;border-radius:6px}

/* agent network */
.network{position:relative;height:420px;background:var(--light)}
.network .copy{position:absolute;left:120px;top:38px;width:560px}
.network .lead{color:var(--blue);font-size:22px;font-weight:600;line-height:1.35}
.network h2{font-size:44px;font-weight:800;line-height:1.15;margin-top:10px}
.network .btn{margin-top:28px;padding:16px 30px;font-size:16px}
.network .portrait{position:absolute;right:80px;bottom:0;width:380px;height:470px;background:linear-gradient(180deg,#d9dde2 0%,#b7bec7 55%,#5f6873 100%);border-radius:6px 6px 0 0}

/* footer */
.footer{height:384px;background:var(--footer);color:#cfd2d6;position:relative}
.footer .brand{position:absolute;left:120px;top:78px;color:var(--white);font-size:24px}
.fcol{position:absolute;top:54px}
.fcol h4{color:var(--white);font-size:20px;font-weight:600;margin-bottom:12px}
.fcol ul{list-style:none;font-size:14px;line-height:1.85}
.fcol.about{left:440px}
.fcol.shop{left:640px}
.fcol.shop .lists{display:flex;gap:60px}
.fcol.links{left:920px}
.legal{position:absolute;left:0;right:0;bottom:0;height:64px;border-top:1px solid var(--footer-line);display:flex;align-items:center;justify-content:space-between;padding:0 60px 0 40px;font-size:13px}
.social{display:flex;gap:14px}
.social span{width:18px;height:18px;border-radius:50%;background:#cfd2d6;display:block}
</style>
</head>
<body>

<header class="topbar">
  <div class="contacts">
    <span><svg width="14" height="14" viewBox="0 0 24 24" fill="#fff"><path d="M6.6 10.8a15.1 15.1 0 0 0 6.6 6.6l2.2-2.2a1 1 0 0 1 1-.25 11.4 11.4 0 0 0 3.6.57 1 1 0 0 1 1 1V20a1 1 0 0 1-1 1A17 17 0 0 1 3 4a1 1 0 0 1 1-1h3.5a1 1 0 0 1 1 1c0 1.25.2 2.45.57 3.57a1 1 0 0 1-.25 1z"/></svg>(555) 318-0472</span>
    <span><svg width="16" height="12" viewBox="0 0 24 18" fill="#fff"><path d="M2 0h20a2 2 0 0 1 2 2v14a2 2 0 0 1-2 2H2a2 2 0 0 1-2-2V2a2 2 0 0 1 2-2zm0 3v1l10 6 10-6V3L12 9z"/></svg>info@BrellowCover.com</span>
  </div>
  <div class="agent">Are you an independent agent? <a href="#">Sign up</a> | <a href="#">Login</a></div>
</header>

<nav class="nav">
  <a class="brand" href="#"><span class="mark"></span>Brellow Cover Insurance, LP</a>
  <div class="menu">
    <a class="active" href="#">Home</a>
    <a href="#">About</a>
    <a href="#">Insurance</a>
    <a href="#">Contact Us</a>
    <a class="btn" href="#">Get a Quote</a>
  </div>
</nav>

<section class="hero">
  <div class="photo" role="img" aria-label="Smiling insurance agent in a suit standing in a bright office with clients meeting behind him"></div>
  <div class="copy">
    <h1>Brellow Cover Insurance, LP</h1>
    <p>Let your local independent agent do the work for you.</p>
    <a class="btn" href="#">Get a Quote</a>
  </div>
</section>

<section class="carriers">
  <h2>Insurance companies we work with</h2>
  <div class="carrier-row">
    <svg class="arrow" viewBox="0 0 24 24"><path d="M15 5l-7 7 7 7" stroke="#1f2430" stroke-width="2.5" fill="none"/></svg>
    <span class="carrier">Varnix</span>
    <span class="carrier">Ostle</span>
    <span class="carrier">Meridale Mutual</span>
    <span class="carrier">Quillor</span>
    <span class="carrier">Dunmarrow</span>
    <span class="carrier">KGZ</span>
    <svg class="arrow" viewBox="0 0 24 24"><path d="M9 5l7 7-7 7" stroke="#1f2430" stroke-width="2.5" fill="none"/></svg>
  </div>
</section>

<section class="welcome">
  <h2>Welcome to Brellow Cover Insurance LP</h2>
  <p>At Brellow Cover Insurance, we understand that your peace of mind is invaluable. Our mission is to protect what matters most to you—your home, your vehicle, your health, and your loved ones. With our comprehensive range of insurance solutions, we are dedicated to safeguarding your assets and providing you with the security you deserve.</p>
  <div class="inquiry">For inquiries, please contact us at<br>(555) 318-0472 or info@BrellowCover.com</div>
</section>

<section class="reviews">
  <div class="kicker">We recommended the best insurance agents for you.</div>
  <h2>See what shoppers like you are saying!</h2>
  <svg class="side-arrow left" width="22" height="22" viewBox="0 0 24 24"><path d="M15 5l-7 7 7 7" stroke="#1f2430" stroke-width="2.5" fill="none"/></svg>
  <svg class="side-arrow right" width="22" height="22" viewBox="0 0 24 24"><path d="M9 5l7 7-7 7" stroke="#3cb44a" stroke-width="2.5" fill="none"/></svg>
  <div class="cards">
    <article class="card">
      <div class="stars">★★★★★</div>
      <h3>Halvern Agency, Inc</h3>
      <div class="loc">Dellbrook, CT</div>
      <blockquote>“ They compared several carriers for our home and car and found a better policy at a lower price. Friendly, fast and always easy to reach. ”</blockquote>
    </article>
    <article class="card">
      <div class="stars">★★★★★</div>
      <h3>Halvern Agency, Inc</h3>
      <div class="loc">Dellbrook, CT</div>
      <blockquote>“ They compared several carriers for our home and car and found a better policy at a lower price. Friendly, fast and always easy to reach. ”</blockquote>
    </article>
    <article class="card">
      <div class="stars">★★★★★</div>
      <h3>Halvern Agency, Inc</h3>
      <div class="loc">Dellbrook, CT</div>
      <blockquote>“ They compared several carriers for our home and car and found a better policy at a lower price. Friendly, fast and always easy to reach. ”</blockquote>
    </article>
  </div>
  <a class="more" href="#">Read More Testimonials</a>
</section>

<section class="network">
  <div class="copy">
    <div class="lead">Find out how to get listed and recommended on Brellow Cover Insurance, LP</div>
    <h2>Are you an independent insurance agent or insurance company?</h2>
    <a class="btn" href="#">Join Our Professional Network</a>
  </div>
  <div class="portrait" role="img" aria-label="Smiling insurance professional working at a laptop"></div>
</section>

<footer class="footer">
  <a class="brand" href="#"><span class="mark"></span>Brellow Cover Insurance, LP</a>
  <div class="fcol about">
    <h4>About Us</h4>
    <ul><li>Excepteur sint</li><li>Occaecat cupidatat</li><li>Proident sunt</li><li>Culpa qui officia</li><li>Deserunt mollit anim</li><li>Est laborum</li></ul>
  </div>
  <div class="fcol shop">
    <h4>Shop Insurance</h4>
    <div class="lists">
      <ul><li>Homeowners</li><li>Auto</li><li>Renters</li><li>Condo</li><li>Flood</li><li>Disability</li></ul>
      <ul><li>Life</li><li>Umbrella</li><li>Health Insurance</li></ul>
    </div>
  </div>
  <div class="fcol links">
    <h4>Quick Links</h4>
    <ul><li>Excepteur sint</li><li>Occaecat cupidatat</li><li>Proident sunt</li><li>Culpa qui officia</li><li>Deserunt mollit anim</li><li>Est laborum</li></ul>
  </div>
  <div class="legal">
    <span>Company ©2020 Company Name All Right Reserved</span>
    <div class="social"><span></span><span></span><span></span><span></span><span></span></div>
  </div>
</footer>

</body>
</html>
```